Wordpress website design for a Herbal Health Care Company

** Outcome of this project is only the design. Only PSD files of the design for unique pages are sufficient.
** There are a number of unique pages in the new site as shown in the wire-frame. However, for the selection of the designer, Homepage, one 2nd tier page (product category) and one 3rd tier page (product page) is sufficient.
We need web design for our for Ayurvedic & Herbal Products Company located in Sri Lanka
Please get the idea about our company by reading the following text
Vision : To be a world class manufacturer and a supplier of highest quality Ayurvedic pharmaceuticals, Herbal health care products, Herbal cosmetics, Essential oils and Oleoresins
Mission : To provide safe and effective Ayurvedic pharmaceuticals, Herbal health care products and Herbal cosmetics, that is of highest quality and integrity, through the incorporation of ancient ayurvedic wisdom with modern technology and scientific management systems for the inprovement of health and longevity of the people.
Policy on Quality : To design, develop, produce and deliver safe, efficacious and consistent quality Herbal health care products based on Ancient Ayurvedic Wisdom using environmentally preferred process technologies and competent personnel towards continual commitment to total customer satisfaction.
(1) Color theme of the website
You can use the color derived from the company logo
(2) Site Map and description of the site
(1) Home
see the wire frame
http://clipmora.net/t/qWxPlKmR4s7T
we need drop-down menu for top menu bar
(2) About Fern Vale [ This is single page with some description + imaged and following sub page links should be placed in this page]
2.1 Board of Directors
2.2 Milestones
2.3 Our Logo
2.4 Production & R&D
2.5 Certification and Awards
2.6 Global Presence
2.7 Investors
2.8 Distribution
(3)Ayurveda Pharmaceuticals [ This is one of the 3 main categories ,Category Main Page should provide an introduction to the category]
Following shows the sub categories of the “Ayurvedic Pharmaceuticals” . each subcategory has different products. We need unique design for Main Category Page and Sub category
3.1 Arista
3.2 Asava
3.3 Coorna
3.4 Lepa
3.5 Gritha
3.7 Guggulu
3.8 Kalka
3.9 Kwatha
3.10 Pana
see the wireframe
http://clipmora.net/t/7KrtVm83BQNN
when you click subcategory , we nee a page like this to list products
http://clipmora.net/t/HXwQ5nDe21
(4) Herbal Health Care Products [ This is one of the 3 main categories]
you do not find subcategories, you have only products listed. we need unique design for this category page + products
This page will consists of category description with image and products listed
see the wire frame
(5) Cosmetics & Spa Products
see the wire frame
(6) Essential Oils & Oleoresins
see the wire frame
(7) Media
We need to put video / image gallery / text . and future events
(8) Investors
related information to investors
we need image + text
(9) CSR
(10) Contact US
contact us form / address / telephone number and google map
(11) Log In
Normal login form
(12) Career
Reference Details
http://clipmora.net/t/9PeLcR4TYJ
http://clipmora.net/t/5MgkDRR2Vu
http://clipmora.net/t/bNqVrTHww
Here is a similar site that should give you some idea how we like the new site to look http://www.velkor.com
Industry/Entity Type
Health Care
Requirements
Must have
- We have 4 main categories in our production line
Quality Ayurvedic pharmaceuticals, Herbal health care products, Herbal cosmetics, Essential oils and Oleoresins
You can use 4 boxes below the slider for it ( This very important to have unique different design for each category with some heading, text and images etc)
Nice to have
- You can suggest any good nice features. Try to keep a clean, natural, relaxing theme, with shades of green, white and orange as per their logo. This can be seen from the project brief attachments. www.velkor.com is an example.
Should not have
- Please avoid dark colours (red) and sad colours (grey, black)

```html
<!DOCTYPE html>
<html lang="en">
<head>
<meta charset="utf-8">
<title>Fern Vale – A Healthy Long Life</title>
<link rel="stylesheet" href="https://fonts.googleapis.com/css2?family=Questrial&family=Ubuntu:ital,wght@1,500&display=swap">
<style>
:root{
  --green:#1f8f45;
  --green-light:#2fa257;
  --green-strip:#3aa461;
  --page:#eeeeee;
  --menu-bg:#e6e6e6;
  --text:#3a3a3a;
  --muted:#666;
  --orange:#f39a1e;
  --rust:#d9471f;
  --white:#ffffff;
}
*{box-sizing:border-box;margin:0;padding:0}
html,body{width:1200px;height:900px;overflow:hidden}
body{background:var(--page);font-family:"Questrial",sans-serif;color:var(--text);position:relative}

.site-header{position:absolute;left:0;top:0;width:1200px;height:101px;background:linear-gradient(var(--green) 0,var(--green) 88px,var(--green-strip) 88px)}
.brand{position:absolute;left:51px;top:9px;width:116px;height:75px;background:var(--white);border-radius:3px;display:flex;align-items:center;justify-content:center;font-size:22px;color:var(--green)}
.tagline{position:absolute;left:225px;top:41px;font-family:"Ubuntu",sans-serif;font-style:italic;font-weight:500;font-size:17px;color:#f4f0c8;letter-spacing:.5px}
.top-nav{position:absolute;right:0;top:15px;display:flex}
.top-nav a{color:var(--white);text-decoration:none;font-size:13px;padding:6px 9px;border-left:1px solid rgba(255,255,255,.45);line-height:18px}
.top-nav a:first-child{border-left:none}
.search{position:absolute;left:1053px;top:63px;width:160px;height:24px;border:1px solid #9fcfae;border-radius:4px;background:linear-gradient(#fff,#e8efe9);font-size:11px;color:#666;padding:5px 7px}

.main-nav{position:absolute;top:115px;left:0;width:1200px;height:34px}
.main-nav a{position:absolute;top:0;height:34px;background:var(--menu-bg);color:var(--text);text-decoration:none;font-size:15px;display:flex;flex-direction:column;justify-content:center;align-items:center;line-height:14px}
.main-nav a small{font-size:9px;align-self:flex-start;padding-left:12px}
.main-nav a .lead{align-self:flex-start;padding-left:12px}
.nav-rule{position:absolute;top:160px;left:199px;width:823px;height:6px;background:radial-gradient(ellipse at center,rgba(0,0,0,.12),transparent 70%)}

.side-photo{position:absolute;top:208px;height:227px}
.side-left{left:0;width:199px;background:linear-gradient(120deg,#f0a0b0,#d8264a 55%,#b81637)}
.side-right{left:1022px;width:178px;background:linear-gradient(180deg,#9eb779,#cfe2e0 55%,#86c96b)}
.slider{position:absolute;left:199px;top:183px;width:823px;height:270px;background:radial-gradient(circle at 35% 30%,#8d8fb8,#5b4d45 45%,#3b2a22);box-shadow:0 8px 10px -6px rgba(0,0,0,.35)}
.slider-base{position:absolute;left:199px;top:453px;width:823px;height:8px;background:#cfcfcf}
.pager{position:absolute;left:545px;top:429px;width:130px;height:36px;background:var(--rust);border-radius:6px 6px 0 0}
.pager svg{display:block}

.section-title{position:absolute;left:220px;top:491px;display:flex;align-items:center;gap:12px;font-size:20px;color:#444}
.section-title i{width:11px;height:13px;background:#d5d5d5;display:block}
.product{position:absolute;top:537px;width:214px;height:214px;border:3px solid var(--orange);background:var(--white);padding:4px}
.product div{width:100%;height:100%}
.p1 div{background:radial-gradient(circle at 50% 55%,#9a9c8a,#b9643a 45%,#fff 75%)}
.p2 div{background:radial-gradient(circle at 50% 55%,#a06a36,#5e8a37 45%,#fff 75%)}
.p3 div{background:radial-gradient(circle at 55% 50%,#4b3a52,#4fa53a 45%,#fff 78%)}

.divider{position:absolute;left:199px;top:803px;width:823px;height:12px;background:radial-gradient(ellipse at center,rgba(0,0,0,.13),transparent 70%)}
.home-icon{position:absolute;left:219px;top:846px}
.about-panel{position:absolute;left:208px;top:876px;width:530px;height:40px;border:1px solid #d4d4d4;border-radius:4px;background:#f6f6f6;display:flex;align-items:center;gap:14px;padding:0 10px;font-size:18px}
.about-panel .num{width:42px;height:22px;background:#ddd;border-radius:3px;font-size:11px;text-align:center;line-height:22px;margin-top:12px}
.testimony{position:absolute;left:757px;top:876px;width:255px;height:40px;background:var(--rust);border-radius:4px 4px 0 0;color:#fff;font-size:19px;display:flex;align-items:center;gap:10px;padding:0 12px}
.testimony i{width:16px;height:14px;background:#e86a42;border-radius:2px;display:block}
</style>
</head>
<body>
<header class="site-header">
  <div class="brand">Fern Vale</div>
  <div class="tagline">“ .. A Healthy Long Life ”</div>
  <nav class="top-nav">
    <a href="#">Media</a><a href="#">Investors</a><a href="#">Careers</a><a href="#">CSR</a><a href="#">Contact Us</a><a href="#">Log In</a>
  </nav>
  <div class="search">Search...</div>
</header>

<nav class="main-nav">
  <a href="#" style="left:273px;width:58px">Home</a>
  <a href="#" style="left:345px;width:129px">About Fern Vale</a>
  <a href="#" style="left:489px;width:84px"><span class="lead">Ayurvedic</span><small>Pharmaceuticals</small></a>
  <a href="#" style="left:588px;width:99px"><span class="lead">Herbal Health</span><small>Care Products</small></a>
  <a href="#" style="left:701px;width:132px"><span class="lead">Cosmetics, Aroma</span><small>&amp; Spa Products</small></a>
  <a href="#" style="left:847px;width:99px"><span class="lead">Essential Oils</span><small>&amp; Oleoresins</small></a>
</nav>
<div class="nav-rule"></div>

<div class="side-photo side-left" role="img" aria-label="Close-up of a pink lily petal"></div>
<div class="side-photo side-right" role="img" aria-label="Glass of herbal drink with lemongrass leaves"></div>
<div class="slider" role="img" aria-label="Tins of dried lavender, rose buds and rolled herbal tea"></div>
<div class="slider-base"></div>
<div class="pager">
  <svg width="130" height="30" viewBox="0 0 130 30">
    <path d="M12 14 L6 9 L12 4 Z" transform="translate(0,4)" fill="#f0a78f"/>
    <circle cx="32" cy="13" r="6" fill="#fff"/>
    <circle cx="48" cy="13" r="6" fill="none" stroke="#f0a78f" stroke-width="2"/>
    <circle cx="64" cy="13" r="6" fill="none" stroke="#f0a78f" stroke-width="2"/>
    <circle cx="80" cy="13" r="6" fill="none" stroke="#f0a78f" stroke-width="2"/>
    <circle cx="96" cy="13" r="6" fill="none" stroke="#f0a78f" stroke-width="2"/>
    <path d="M118 8 L124 13 L118 18 Z" fill="#f0a78f"/>
  </svg>
</div>

<h2 class="section-title"><i></i>Fern Vale Products</h2>
<div class="product p1" style="left:274px"><div role="img" aria-label="Stone mortar with spices, cinnamon and herbal oil"></div></div>
<div class="product p2" style="left:517px"><div role="img" aria-label="Wooden mortar filled with fresh herbs"></div></div>
<div class="product p3" style="left:757px"><div role="img" aria-label="Bunch of fresh green and purple basil leaves"></div></div>

<div class="divider"></div>
<svg class="home-icon" width="16" height="16" viewBox="0 0 16 16"><path d="M8 1 L15 8 H13 V15 H10 V10 H6 V15 H3 V8 H1 Z" fill="#bdbdbd"/></svg>
<div class="about-panel"><span class="num">10</span>About Fern Vale</div>
<div class="testimony"><i></i>Testimony</div>
</body>
</html>
```